Tralha Cesto Website

Tralha Cesto is a brazilian Self Storage in a Box where customers can store all the clutter that they have out of their houses. We deliver one or more boxes at their homes, they fill the boxes with their stuff and we store it for them.

"Tralha" means something like "mess" in portuguese. So the name would means something like "Mess Box" or "Clutter Box".

How it works:
1) The customer asks for 1 or more boxes.
2) Tralha Cesto leaves the boxes at their houses
3) The clients fill the boxes with their stuff
4) Customers call Tralha Cesto for the pick up
5) We get the boxes and store them
6) When the customer wants the box back they can order it online or by phone and wait for the box delivery.
-

We have already produced a flyer to launch the service. You can see this flyer at "Project Files".

We want the website to have a startup "look and fell". Here are some websites of similar services that we like very much.
- www.crateowl.example
- www.stowpod.example

We are planning this launching website to have only 2 pages. The Landing Page and a FAQ page. We are producing an explainer video. The proposed designs must think about a special place to place the video.

We are still writing it´s content but you can use the flyer as a reference.

Thanks.
Updates

Project Deadline Extended
Reason: The project was refundable but as we have already received good design options, now we are turning it to Non Refundable and giving more time for new designers to send their proposals. Thanks.

Project Deadline Extended

Target Market(s)

Young couples having kids
Students
Families in need of more space at home

Industry/Entity Type

Store

Requirements
Must have
• Special place to place the explainer video (still being produced).

How it works drawing. You can use the one on the flyer or draw a new one (recomended).

Transparent box drawings (showing it´s content). I will serve to show the clients what they can store with the service.

Clutter Room Before/After Pic/drawings (showing how the service can benefit the client).

```html
<!DOCTYPE html>
<html lang="pt-BR">
<head>
<meta charset="utf-8">
<title>Tralha Cesto — Self Storage</title>
<link rel="stylesheet" href="https://fonts.googleapis.com/css2?family=Lato:wght@300;400;700;900&display=swap">
<style>
:root{
  --orange:#f7941d;
  --orange-dark:#e2800c;
  --blue:#1b6fc2;
  --blue-dark:#1460ad;
  --ink:#3a3a3a;
  --grey:#7a7a7a;
  --light:#f1f1f1;
  --paper:#ffffff;
  --footer:#343434;
  --footer-bottom:#2a2a2a;
  --video:#3b3d3f;
}
*{box-sizing:border-box;margin:0;padding:0}
html,body{width:1200px;height:2647px;overflow:hidden}
body{font-family:"Lato",sans-serif;color:var(--ink);background:var(--paper);position:relative}
.abs{position:absolute}

/* header */
.site-header{position:absolute;left:0;top:0;width:1200px;height:134px;background:var(--paper);border-top:3px solid var(--blue)}
.brand{position:absolute;left:88px;top:78px;display:flex;align-items:center;gap:10px;font-weight:700;font-size:26px;color:var(--blue)}
.brand-dot{width:22px;height:22px;border-radius:50%;background:var(--orange)}
.phone{position:absolute;right:88px;top:26px;display:flex;align-items:center;gap:10px;font-weight:700;font-size:24px;color:var(--orange)}
.main-nav{position:absolute;right:290px;top:98px;display:flex;gap:32px;font-size:15px;color:var(--grey)}
.main-nav .active{color:var(--blue);font-weight:700;border-bottom:2px solid var(--orange);padding-bottom:4px}
.quote-btn{position:absolute;left:911px;top:88px;width:201px;height:36px;background:var(--blue);color:#fff;font-weight:900;font-size:17px;display:flex;align-items:center;justify-content:center;border-radius:3px}

/* hero */
.hero-photo{position:absolute;left:0;top:134px;width:1200px;height:351px;background:linear-gradient(180deg,#8fb6dc 0%,#b9cfe0 35%,#b7a79a 60%,#8a8f84 100%)}
.hero-illustration{position:absolute;left:300px;top:150px;width:510px;height:380px;background:linear-gradient(180deg,#f2a23a 0%,#3d4f8a 45%,#c9ccd1 75%,#6d7fa5 100%);border-radius:6px;opacity:.92}
.hero-title{position:absolute;left:88px;top:250px;font-size:36px;line-height:38px;letter-spacing:-1px;color:var(--orange);font-weight:900;text-transform:uppercase}
.hero-title .light{display:block;color:#fff;font-weight:300}
.feature-band{position:absolute;left:0;top:485px;width:1200px;height:238px;background:var(--orange)}
.feature{position:absolute;top:97px;width:320px;display:flex;gap:14px;color:#fff}
.feature-icon{flex:none;width:82px;height:82px;border:3px solid #fff;border-radius:16px;display:flex;align-items:center;justify-content:center}
.feature h3{font-size:20px;font-weight:700;line-height:22px}
.feature p{font-size:13px;line-height:15px;margin-top:2px}
.feature .more{font-size:11px;opacity:.6;margin-top:6px}

/* how it works */
.how{position:absolute;left:0;top:723px;width:1200px;height:327px;background:var(--light)}
.section-title{font-weight:300;color:var(--blue)}
.how .section-title{position:absolute;left:88px;top:44px;font-size:37px}
.step{position:absolute;top:118px;width:220px;text-align:center}
.step-art{margin:0 auto;width:130px;height:94px;border-radius:50%;background:radial-gradient(circle,#bdbdbd 0%,#d8d8d8 60%,var(--light) 72%)}
.step p{margin-top:14px;font-size:12.5px;line-height:15px;color:var(--blue)}
.step-arrow{position:absolute;top:157px}

/* video */
.video{position:absolute;left:0;top:1050px;width:1200px;height:365px;background:linear-gradient(180deg,#4b4e50,#2f3133)}
.video h2{position:absolute;width:1200px;top:116px;text-align:center;font-size:40px;font-weight:300;color:#e9e9e9}
.play{position:absolute;left:563px;top:172px}

/* before after */
.showcase{position:absolute;left:0;top:1415px;width:1200px;height:491px;background:#f7f7f7}
.showcase h2{position:absolute;top:50px;font-size:23px;line-height:28px;font-weight:400;color:var(--blue)}
.photo{position:absolute;top:129px;width:224px;height:133px;border:3px solid #555;border-radius:6px}
.photo.before{left:88px;background:linear-gradient(135deg,#6c6f78,#3e4048 60%,#9a8f80)}
.photo.after{left:342px;background:linear-gradient(135deg,#7a5a3a,#4a3424 55%,#c9a77a)}
.photo-label{position:absolute;top:279px;width:224px;text-align:center;font-size:12px;font-weight:700;color:var(--blue)}
.bullets{position:absolute;left:88px;top:298px;list-style:none;font-size:14px;line-height:23px;color:var(--ink)}
.bullets li{display:flex;align-items:center;gap:8px}
.bullets li::before{content:"";width:10px;height:10px;border-radius:50%;background:var(--blue)}
.showcase .copy{position:absolute;left:88px;top:370px;width:440px;font-size:13px;line-height:16px;color:var(--grey)}
.divider{position:absolute;left:597px;top:50px;width:1px;height:360px;background:#d6d6d6}
.plan{position:absolute;top:126px;width:229px;height:294px;border-radius:4px;color:#fff;text-align:center;overflow:hidden}
.plan.large{left:632px;background:var(--orange)}
.plan.small{left:882px;background:var(--blue)}
.plan-art{height:100px;display:flex;align-items:center;justify-content:center}
.plan-art span{display:block;width:96px;height:70px;border-radius:3px}
.plan.large .plan-art span{background:linear-gradient(160deg,#3f7fc0,#8ab4de)}
.plan.small .plan-art span{background:linear-gradient(160deg,#f7a33c,#7da7d6)}
.plan-price{background:#fbe0bb;color:var(--ink);font-size:11px;padding:6px 0 5px}
.plan.small .plan-price{background:#bfd9f1}
.plan-price strong{display:block;font-size:19px;font-weight:400;color:#333;margin-top:1px}
.plan-price strong b{font-weight:700}
.plan-row{font-size:11.5px;line-height:14px;padding:12px 16px;border-bottom:1px solid rgba(255,255,255,.35)}
.plan-row:last-child{border-bottom:none}

/* security */
.security{position:absolute;left:0;top:1906px;width:1200px;height:403px;background:var(--light)}
.badge{position:absolute;left:538px;top:-20px;width:124px;height:124px;border-radius:50%;background:#fff;border:6px solid var(--blue);display:flex;align-items:center;justify-content:center;font-weight:700;font-size:15px;color:var(--blue)}
.security h2{position:absolute;top:128px;width:1200px;text-align:center;font-size:40px;font-weight:400;color:var(--blue)}
.security .lead{position:absolute;top:175px;width:1200px;text-align:center;font-size:19px;color:var(--blue)}
.security .copy{position:absolute;left:240px;top:203px;width:720px;text-align:center;font-size:13px;line-height:16px;color:var(--grey)}
.hazard{position:absolute;top:275px;width:76px;height:76px;border-radius:50%;border:3px solid #555;background:#fff;display:flex;align-items:center;justify-content:center}

/* press */
.press{position:absolute;left:0;top:2309px;width:1200px;height:88px;background:var(--blue)}
.press-badge{position:absolute;top:34px;height:20px;border-radius:3px;background:#1a2533}

/* footer */
.site-footer{position:absolute;left:0;top:2397px;width:1200px;height:212px;background:var(--footer);color:#d7d7d7}
.site-footer h4{font-size:20px;font-weight:700;color:#fff;margin-bottom:10px}
.foot-col{position:absolute;top:40px}
.foot-col ul{list-style:none;font-size:13px;line-height:19.5px}
.contact li{display:flex;gap:12px;align-items:flex-start}
.contact svg{flex:none;margin-top:3px}
.foot-rule{position:absolute;top:62px;width:1px;height:110px;background:#555}
.social{display:flex;gap:12px;margin-top:8px}
.social span{width:36px;height:36px;border-radius:50%;border:2px solid #d7d7d7}
.foot-brand{position:absolute;left:940px;top:90px;display:flex;align-items:center;gap:10px;font-weight:700;font-size:24px;color:#e8e8e8}
.foot-brand i{width:18px;height:18px;border-radius:50%;background:#e8e8e8}
.legal{position:absolute;left:0;top:2609px;width:1200px;height:38px;background:var(--footer-bottom);color:#9a9a9a;font-size:12px}
.legal span{position:absolute;top:12px}
</style>
</head>
<body>

<header class="site-header">
  <div class="brand"><span class="brand-dot"></span>Tralha Cesto</div>
  <div class="phone">
    <svg width="28" height="28" viewBox="0 0 28 28"><circle cx="14" cy="14" r="12.5" fill="none" stroke="#f7941d" stroke-width="2"/><path d="M9 8c1-1 2-1 3 0l1.5 2.5c.4.8 0 1.5-.6 2l-.8.6c.8 1.8 2 3 3.8 3.8l.6-.8c.5-.6 1.2-1 2-.6L21 17c1 1 1 2 0 3-1.5 1.5-4 1-7-2s-3.5-5.5-2-7z" fill="#f7941d"/></svg>
    (21) 4002-1870
  </div>
  <nav class="main-nav">
    <span class="active">How it Works</span><span>Pricing</span><span>Security</span><span>Login</span>
  </nav>
  <div class="quote-btn">GET FREE QUOTE</div>
</header>

<section class="hero">
  <div class="hero-photo" role="img" aria-label="Blurred photo of a row of colourful storage containers under a blue sky"></div>
  <div class="feature-band">
    <div class="feature" style="left:88px">
      <div class="feature-icon"><svg width="50" height="50" viewBox="0 0 50 50"><circle cx="25" cy="25" r="20" fill="none" stroke="#fff" stroke-width="3"/><rect x="15" y="22" width="20" height="14" rx="2" fill="#fff"/><path d="M19 22v-4a6 6 0 0 1 12 0v4" fill="none" stroke="#fff" stroke-width="3"/></svg></div>
      <div><h3>Segurança:</h3><p>tenha suas coisas armazenadas em um ambiente seguro, monitorado 24 horas por dia</p><p class="more">Saiba mais</p></div>
    </div>
    <div class="feature" style="left:455px">
      <div class="feature-icon"><svg width="50" height="50" viewBox="0 0 50 50"><circle cx="25" cy="25" r="20" fill="none" stroke="#fff" stroke-width="3"/><path d="M15 25l7 7 14-15" fill="none" stroke="#fff" stroke-width="4" stroke-linecap="round" stroke-linejoin="round"/></svg></div>
      <div><h3>Praticidade:</h3><p>escolha o recebimento de suas coisas em sua casa ou em um de nossos Pontos de Coleta no Flamengo...</p><p class="more">Saiba mais</p></div>
    </div>
    <div class="feature" style="left:798px">
      <div class="feature-icon"><svg width="50" height="50" viewBox="0 0 50 50"><circle cx="25" cy="25" r="20" fill="none" stroke="#fff" stroke-width="3"/><path d="M12 26l7-6h6l5 4 8-4" fill="none" stroke="#fff" stroke-width="3" stroke-linejoin="round"/><path d="M17 30l5 4 4-2 4 1 6-5" fill="none" stroke="#fff" stroke-width="3" stroke-linejoin="round"/></svg></div>
      <div><h3>Economia:</h3><p>aproveite melhor o espaço que você já tem dentro de casa</p><p class="more">Saiba mais</p></div>
    </div>
  </div>
  <div class="hero-illustration" role="img" aria-label="Illustration of a delivery worker holding a storage box above delivery trucks, a house, a bicycle, a sofa and a lamp"></div>
  <h1 class="hero-title">Get<br>Access to your stuff<span class="light">Whenever you need</span></h1>
</section>

<section class="how">
  <h2 class="section-title">How it works</h2>
  <div class="step" style="left:66px"><div class="step-art" role="img" aria-label="Grey icon of a person asking for a box at home"></div><p>Solicite a Tralha Cesto<br>em sua casa</p></div>
  <svg class="step-arrow" style="left:280px" width="44" height="30" viewBox="0 0 44 30"><path d="M0 10h24V0l20 15-20 15V20H0z" fill="#f7941d"/></svg>
  <div class="step" style="left:331px"><div class="step-art" role="img" aria-label="Grey icon of belongings being packed into a box"></div><p>Guarde tudo o que quiser,<br>tranque a caixa e guarde a<br>chave</p></div>
  <svg class="step-arrow" style="left:550px" width="44" height="30" viewBox="0 0 44 30"><path d="M0 10h24V0l20 15-20 15V20H0z" fill="#f7941d"/></svg>
  <div class="step" style="left:613px"><div class="step-art" role="img" aria-label="Grey icon of a truck collecting the box from a house"></div><p>Agende a<br>coleta da caixa</p></div>
  <svg class="step-arrow" style="left:836px" width="44" height="30" viewBox="0 0 44 30"><path d="M0 10h24V0l20 15-20 15V20H0z" fill="#f7941d"/></svg>
  <div class="step" style="left:877px;width:240px"><div class="step-art" role="img" aria-label="Grey icon of ordering the box back by phone or computer"></div><p>Tenha acesso às suas coisas sempre quiser solicitando a entrega da Tralha Cesto em sua casa ou em um de nossos Pontos de Coleta</p></div>
</section>

<section class="video" role="img" aria-label="Explainer video placeholder over a dark photo of shipping containers">
  <h2>Watch How We Work</h2>
  <svg class="play" width="74" height="74" viewBox="0 0 74 74"><circle cx="37" cy="37" r="33" fill="none" stroke="#e0e0e0" stroke-width="5"/><path d="M29 22l24 15-24 15z" fill="#e0e0e0"/></svg>
</section>

<section class="showcase">
  <h2 style="left:88px">Transforme o seu quarto da tralha em um<br>quarto de verdade</h2>
  <div class="photo before" role="img" aria-label="Photo of a cluttered room before storage"></div>
  <div class="photo after" role="img" aria-label="Photo of the same room tidy after storage"></div>
  <div class="photo-label" style="left:88px">ANTES</div>
  <div class="photo-label" style="left:342px">DEPOIS</div>
  <ul class="bullets">
    <li>A família está crescendo?</li>
    <li>Quer receber bem aquele parente?</li>
    <li>Está se mudando para um lugar menor?</li>
  </ul>
  <p class="copy">Reconquiste o espaço da sua casa guardando tudo aquilo que você não usa no seu dia-a-dia com a Tralha Cesto.<br>Não use o precioso espaço da sua casa como depósito. Deixe que a Tralha Cesto guarda as coisas para você.</p>
  <div class="divider"></div>
  <h2 style="left:620px">Escolha a caixa que melhor se enquadra em suas<br>necessidades:</h2>
  <div class="plan large">
    <div class="plan-art"><span role="img" aria-label="Drawing of a large transparent box holding a television and household items"></span></div>
    <div class="plan-price">a partir de<strong>R$<b>69,00</b> / mês</strong></div>
    <div class="plan-row">Dimensões: 120cm (C) x 80cm (L) x 92,5cm (A). Volume total: 800 Litros</div>
    <div class="plan-row">Entrega nos pontos de coleta: <b>R$ 9,90</b></div>
    <div class="plan-row">Entrega em domicílio: <b>R$29,90</b></div>
  </div>
  <div class="plan small">
    <div class="plan-art"><span role="img" aria-label="Drawing of a small transparent box holding toys and books"></span></div>
    <div class="plan-price">a partir de<strong>R$<b>14,90</b> / mês</strong></div>
    <div class="plan-row">Dimensões: 78cm (C) x 56cm (L) x 41cm (A). Volume total: 130 Litros</div>
    <div class="plan-row">Entrega nos pontos de coleta: <b>R$ 4,90</b></div>
    <div class="plan-row">Entrega em domicílio: <b>R$14,90</b></div>
  </div>
</section>

<section class="security">
  <div class="badge">Tralha Cesto</div>
  <h2>Security is our Priority</h2>
  <p class="lead">Professional storage and 24hr security keep your things safe from the hazards at home</p>
  <p class="copy">We understand how it feels to have things you care about placed in the protection of others, so we've made the security of your boxes the greatest priority at Tralha Cesto. With storage from Tralha Cesto, you're protected from:</p>
  <div class="hazard" style="left:347px"><svg width="40" height="40" viewBox="0 0 40 40"><rect x="4" y="4" width="32" height="32" rx="4" fill="#f7941d"/><circle cx="20" cy="20" r="8" fill="none" stroke="#fff" stroke-width="3"/></svg></div>
  <div class="hazard" style="left:488px"><svg width="40" height="40" viewBox="0 0 40 40"><path d="M20 4c2 8 10 11 10 21a10 10 0 0 1-20 0c0-6 4-8 5-13 2 3 3 5 3 8 2-4 3-9 2-16z" fill="#f7941d"/><path d="M6 34h28" stroke="#1b6fc2" stroke-width="3"/></svg></div>
  <div class="hazard" style="left:629px"><svg width="40" height="40" viewBox="0 0 40 40"><path d="M20 4c5 9 12 15 12 22a12 12 0 0 1-24 0c0-7 7-13 12-22z" fill="#f7941d"/><path d="M14 26a6 6 0 0 0 6 6" fill="none" stroke="#1b6fc2" stroke-width="3"/></svg></div>
  <div class="hazard" style="left:774px"><svg width="40" height="40" viewBox="0 0 40 40"><circle cx="20" cy="20" r="14" fill="#f7941d"/><path d="M4 20h9l3-7 4 14 3-7h13" fill="none" stroke="#1b6fc2" stroke-width="3" stroke-linejoin="round"/></svg></div>
</section>

<section class="press" aria-label="Featured in the press">
  <div class="press-badge" style="left:300px;width:118px"></div>
  <div class="press-badge" style="left:485px;width:96px"></div>
  <div class="press-badge" style="left:648px;width:68px"></div>
  <div class="press-badge" style="left:777px;width:128px"></div>
</section>

<footer class="site-footer">
  <div class="foot-col" style="left:88px">
    <h4>Special Links</h4>
    <ul><li>Frequently Asked Questions</li><li>In the Press</li><li>Jobs at Tralha Cesto</li><li>Privacy Policy</li><li>Shipment &amp; Storage</li><li>Terms of Service</li><li>Blog</li></ul>
  </div>
  <div class="foot-rule" style="left:320px"></div>
  <div class="foot-col contact" style="left:361px">
    <h4>Contact Us</h4>
    <ul>
      <li><svg width="12" height="12" viewBox="0 0 12 12"><path d="M2 1c.8-.6 1.5-.5 2 .3l.8 1.6c.3.6 0 1-.4 1.3l-.4.3c.6 1.4 1.5 2.3 2.9 2.9l.3-.4c.3-.4.7-.7 1.3-.4l1.6.8c.8.5.9 1.2.3 2-1 1.2-3 1-5.4-1.4S.8 2 2 1z" fill="#d7d7d7"/></svg>(21) 4002-1870</li>
      <li><svg width="14" height="12" viewBox="0 0 14 12"><rect x="1" y="1" width="12" height="9" fill="none" stroke="#d7d7d7" stroke-width="1.4"/><path d="M1 1l6 5 6-5" fill="none" stroke="#d7d7d7" stroke-width="1.4"/></svg>contato@tralhacesto.example</li>
      <li><svg width="12" height="14" viewBox="0 0 12 14"><path d="M6 0a5 5 0 0 1 5 5c0 3.5-5 9-5 9S1 8.5 1 5a5 5 0 0 1 5-5z" fill="#d7d7d7"/><circle cx="6" cy="5" r="2" fill="#343434"/></svg>Tralha Cesto Simple Urban Storage<br>72 Rua das Caixas, 2º andar<br>Rio de Janeiro, RJ</li>
    </ul>
  </div>
  <div class="foot-rule" style="left:620px"></div>
  <div class="foot-col" style="left:673px">
    <h4>Follow Us On</h4>
    <div class="social"><span></span><span></span><span></span></div>
  </div>
  <div class="foot-rule" style="left:883px"></div>
  <div class="foot-brand"><i></i>Tralha Cesto</div>
</footer>
<div class="legal"><span style="left:88px">© 2013, TralhaCesto.example</span><span style="right:88px">Terms | Privacy</span></div>

</body>
</html>
```